Bramwell Crest Electric van design

Looking to design a wrap for a 2021 varenta cargolux high roof using orange black and dark grey colors like in the logo

```html
<!DOCTYPE html>
<html lang="en">
<head>
<meta charset="utf-8">
<title>Bramwell Crest Electric – Van Wrap</title>
<link rel="stylesheet" href="https://fonts.googleapis.com/css2?family=Montserrat:wght@500;700&display=swap">
<style>
  :root {
    --orange: #e8542a;
    --charcoal: #2d2d2f;
    --charcoal-deep: #1d1d1f;
    --white: #ffffff;
    --glass: #3c4146;
    --tail: #b3261e;
    --backdrop: #e6e6e6;
    --wheel-hub: #7a7a7a;
  }
  html, body {
    margin: 0;
    padding: 0;
    width: 1200px;
    height: 3440px;
    overflow: hidden;
    background: var(--backdrop);
    font-family: "Montserrat", sans-serif;
  }
  .sheet { width: 1200px; height: 3440px; position: relative; }
  .view { position: absolute; left: 0; width: 1200px; }
  .view--side { top: 0; height: 735px; }
  .view--quarter { top: 735px; height: 900px; }
  .view--rear { top: 1635px; height: 900px; }
  .view--front { top: 2535px; height: 905px; }
  .view svg { position: absolute; display: block; }
  .defs { position: absolute; width: 0; height: 0; }
  .brand-name { font-family: "Montserrat", sans-serif; font-weight: 700; }
  .contact { font-family: "Montserrat", sans-serif; font-weight: 700; fill: var(--white); }
</style>
</head>
<body>
<main class="sheet">

  <svg class="defs" aria-hidden="true">
    <defs>
      <clipPath id="side-body-clip">
        <path d="M20,60 Q20,20 60,20 L780,20 Q810,20 830,50 L905,170 Q1010,195 1080,255 Q1120,290 1120,330 L1120,370 L20,370 Z"/>
      </clipPath>

      <symbol id="van-side" viewBox="0 0 1140 430">
        <g clip-path="url(#side-body-clip)">
          <rect class="wrap-base" x="0" y="0" width="1140" height="430" fill="var(--white)"/>
          <path class="wrap-dark" d="M0,0 L300,0 C250,80 260,200 340,232 L830,232 C870,234 890,262 905,300 L1140,300 L1140,430 L0,430 Z" fill="var(--charcoal)"/>
          <path class="wrap-stripe" d="M320,168 L820,168 C865,168 888,200 905,255 L945,370 L885,370 L852,282 C842,250 822,232 792,232 L340,232 C330,210 322,190 320,168 Z" fill="var(--orange)"/>
          <path class="cab-window" d="M862,62 L915,62 Q930,62 940,80 L990,168 L862,168 Z" fill="var(--glass)"/>
        </g>
        <circle class="brand-disc-ring" cx="172" cy="192" r="158" fill="var(--charcoal)"/>
        <circle class="brand-disc" cx="172" cy="192" r="146" fill="var(--orange)"/>
        <circle cx="172" cy="192" r="138" fill="none" stroke="var(--white)" stroke-width="3"/>
        <text class="brand-name" x="348" y="92" font-size="50" letter-spacing="3" fill="var(--charcoal)">BRAMWELL CREST</text>
        <text class="brand-name" x="348" y="150" font-size="50" fill="var(--charcoal)">Electric</text>
        <text class="contact" x="350" y="212" font-size="30">555.014.2290</text>
        <text class="contact" x="580" y="208" font-size="15">bramwellcrestelectricinc.com</text>
        <circle cx="262" cy="372" r="56" fill="var(--charcoal-deep)"/>
        <circle cx="262" cy="372" r="26" fill="var(--wheel-hub)"/>
        <circle cx="968" cy="372" r="56" fill="var(--charcoal-deep)"/>
        <circle cx="968" cy="372" r="26" fill="var(--wheel-hub)"/>
      </symbol>

      <symbol id="van-rear" viewBox="0 0 560 720">
        <path class="rear-doors" d="M45,60 Q45,20 95,20 L465,20 Q515,20 515,60 L535,640 L25,640 Z" fill="var(--charcoal)"/>
        <line class="door-seam" x1="280" y1="22" x2="280" y2="640" stroke="var(--charcoal-deep)" stroke-width="3"/>
        <circle class="brand-disc" cx="280" cy="150" r="82" fill="var(--orange)"/>
        <circle cx="280" cy="150" r="76" fill="none" stroke="var(--white)" stroke-width="2"/>
        <text class="brand-name" x="280" y="318" font-size="42" letter-spacing="3" text-anchor="middle" fill="var(--white)">BRAMWELL CREST</text>
        <text class="brand-name" x="280" y="372" font-size="42" text-anchor="middle" fill="var(--white)">Electric</text>
        <rect class="phone-band" x="70" y="398" width="420" height="62" fill="var(--orange)"/>
        <text class="contact" x="280" y="445" font-size="42" text-anchor="middle">555.014.2290</text>
        <text class="contact" x="280" y="572" font-size="20" text-anchor="middle">bramwellcrestelectricinc.com</text>
        <rect class="tail-light" x="14" y="370" width="22" height="150" rx="6" fill="var(--tail)"/>
        <rect class="tail-light" x="524" y="370" width="22" height="150" rx="6" fill="var(--tail)"/>
        <rect class="bumper" x="30" y="640" width="500" height="50" rx="10" fill="var(--charcoal-deep)"/>
      </symbol>
    </defs>
  </svg>

  <section class="view view--side" aria-label="Driver-side panel">
    <svg x="0" y="0" style="left:30px; top:150px" width="1140" height="430" viewBox="0 0 1140 430">
      <use href="#van-side"/>
    </svg>
  </section>

  <section class="view view--quarter" aria-label="Rear and side panels together">
    <svg style="left:150px; top:110px" width="360" height="463" viewBox="0 0 560 720">
      <use href="#van-rear"/>
    </svg>
    <svg style="left:530px; top:140px" width="640" height="241" viewBox="0 0 1140 430">
      <use href="#van-side"/>
    </svg>
  </section>

  <section class="view view--rear" aria-label="Rear doors">
    <svg style="left:290px; top:20px" width="620" height="797" viewBox="0 0 560 720">
      <use href="#van-rear"/>
    </svg>
  </section>

  <section class="view view--front" aria-label="Front and hood">
    <svg style="left:270px; top:60px" width="660" height="800" viewBox="0 0 660 800">
      <path class="front-roof" d="M90,120 Q110,60 180,55 L480,55 Q550,60 570,120 L610,330 L50,330 Z" fill="var(--white)"/>
      <path class="windshield" d="M110,160 Q120,125 160,122 L500,122 Q540,125 550,160 L575,320 L85,320 Z" fill="var(--glass)"/>
      <path class="hood-edge" d="M40,335 L620,335 L640,480 L20,480 Z" fill="var(--white)"/>
      <path class="hood-stripe-left" d="M40,335 L100,335 Q75,400 95,480 L20,480 Z" fill="var(--orange)"/>
      <path class="hood-stripe-right" d="M560,335 L620,335 L640,480 L565,480 Q585,400 560,335 Z" fill="var(--orange)"/>
      <path class="hood" d="M100,335 L560,335 Q585,400 565,480 L95,480 Q75,400 100,335 Z" fill="var(--charcoal)"/>
      <circle class="brand-disc" cx="200" cy="412" r="36" fill="var(--orange)"/>
      <text class="brand-name" x="255" y="405" font-size="29" letter-spacing="2" fill="var(--white)">BRAMWELL CREST</text>
      <text class="brand-name" x="255" y="440" font-size="29" fill="var(--white)">Electric</text>
      <rect class="grille" x="60" y="480" width="540" height="150" rx="18" fill="var(--charcoal-deep)"/>
      <rect class="bumper" x="30" y="630" width="600" height="110" rx="30" fill="var(--charcoal)"/>
      <rect class="headlight" x="25" y="470" width="70" height="50" rx="14" fill="var(--backdrop)"/>
      <rect class="headlight" x="565" y="470" width="70" height="50" rx="14" fill="var(--backdrop)"/>
    </svg>
  </section>

</main>
</body>
</html>
```